Business Card for: Bramwell Financial Advisory Services Inc.

provide strategic financial advisory services to companies in the areas of corporate finance, mergers and acquisitions, executive coaching and strategic planning

Target Market(s)

Companies, banks, accountants, lawyers

Industry/Entity Type

High end business consulting in corporate finance, mergers and acquisitions, consulting

Contact Information for Business Card

Name of company, Name: xxxxxx xxxxxx , CEO, - phone number: 1-xxx-xxx-xxxx, - email address,

Requirements
Must have
• Must be professional and simple.
Nice to have
• simple, straight graphics, must give the impression that we are trustworthy, professional, competent
Should not have
• loud colors, loud design features

```html
<!DOCTYPE html>
<html lang="en">
<head>
<meta charset="UTF-8">
<title>Bramwell Financial Advisory Services Inc. — Business Card</title>
<link rel="stylesheet" href="https://fonts.googleapis.com/css2?family=Poppins:wght@400;500;600&display=swap">
<style>
  :root {
    --backdrop: #adadad;
    --card-white: #ffffff;
    --ink-dark: #2b2b2b;
    --ink-muted: #5d5d5d;
    --rule: #bdbdbd;
    --sky: #4ac8e3;
    --ocean: #0394cc;
    --deep: #0373b7;
    --grad-light: #3ec2e0;
    --grad-dark: #0674b6;
  }
  * { box-sizing: border-box; margin: 0; padding: 0; }
  html, body {
    width: 1093px; height: 1200px; overflow: hidden;
    background: var(--backdrop);
    font-family: "Poppins", sans-serif;
  }
  .card {
    position: absolute; left: 265px;
    width: 580px; height: 356px;
    border-radius: 24px; overflow: hidden;
  }
  .card-front { top: 226px; background: var(--card-white); }
  .card-back {
    top: 621px;
    background: linear-gradient(30deg, var(--grad-dark) 0%, var(--ocean) 50%, var(--grad-light) 100%);
    display: flex; align-items: center; justify-content: center;
  }

  .brand {
    position: absolute; left: 20px; top: 138px; width: 250px;
    text-align: center;
    font-weight: 500; color: var(--ink-dark);
  }
  .brand .line { display: block; white-space: nowrap; }
  .brand .line-lead { font-size: 44px; line-height: 1.05; letter-spacing: -0.5px; }
  .brand .line-sub { font-size: 13.5px; line-height: 1.4; }

  .divider {
    position: absolute; left: 288px; top: 74px;
    width: 1px; height: 209px; background: var(--rule);
  }

  .person { position: absolute; left: 311px; top: 100px; }
  .person-name { font-size: 27px; font-weight: 400; color: var(--ink-dark); line-height: 1.1; white-space: nowrap; }
  .person-name strong { font-weight: 600; }
  .person-title { font-size: 17px; color: var(--ink-muted); line-height: 1.3; }

  .contacts { position: absolute; left: 309px; top: 174px; list-style: none; }
  .contact-item {
    display: flex; align-items: center; gap: 7px;
    font-size: 17px; color: var(--ink-muted); height: 26.5px; white-space: nowrap;
  }
  .contact-icon { width: 20px; height: 20px; border-radius: 3px; flex: none; }
  .contact-phone .contact-icon { background: var(--sky); }
  .contact-email .contact-icon { background: var(--ocean); }
  .contact-web .contact-icon { background: var(--deep); }

  .accent-band { position: absolute; left: 0; bottom: 0; width: 580px; height: 12px; }

  .brand-back {
    color: #ffffff; font-weight: 500; text-align: center;
    margin-top: 40px;
  }
  .brand-back .line { display: block; white-space: nowrap; }
  .brand-back .line-lead { font-size: 64px; line-height: 1.05; letter-spacing: -1px; }
  .brand-back .line-sub { font-size: 22px; line-height: 1.3; }
</style>
</head>
<body>
  <section class="card card-front" aria-label="Business card front">
    <p class="brand">
      <span class="line line-lead">Bramwell</span>
      <span class="line line-sub">Financial Advisory Services Inc.</span>
    </p>

    <div class="divider"></div>

    <div class="person">
      <h1 class="person-name">Daniel <strong>Hartley</strong></h1>
      <p class="person-title">Managing Director</p>
    </div>

    <ul class="contacts">
      <li class="contact-item contact-phone">
        <svg class="contact-icon" viewBox="0 0 20 20" aria-hidden="true">
          <path d="M6 4.5c.6-.4 1.2-.2 1.5.3l1 1.8c.3.5.1 1-.3 1.3l-.7.5c.6 1.3 1.6 2.4 2.9 3l.5-.7c.3-.4.9-.6 1.3-.3l1.8 1c.5.3.7 1 .3 1.5l-.7.9c-.5.6-1.4.8-2.1.5C8.6 13.2 6.8 11.4 5.7 8.5c-.3-.8-.1-1.7.5-2.2z" fill="#fff"/>
        </svg>
        <span>1-555-014-2290</span>
      </li>
      <li class="contact-item contact-email">
        <svg class="contact-icon" viewBox="0 0 20 20" aria-hidden="true">
          <rect x="4" y="6" width="12" height="8.5" fill="none" stroke="#fff" stroke-width="1.3"/>
          <path d="M4 6l6 5 6-5M4 14.5l4.5-4M16 14.5l-4.5-4" fill="none" stroke="#fff" stroke-width="1.1"/>
        </svg>
        <span>info@bramwellfa.com</span>
      </li>
      <li class="contact-item contact-web">
        <svg class="contact-icon" viewBox="0 0 20 20" aria-hidden="true">
          <circle cx="10" cy="10" r="5.5" fill="none" stroke="#fff" stroke-width="1.2"/>
          <ellipse cx="10" cy="10" rx="2.4" ry="5.5" fill="none" stroke="#fff" stroke-width="1"/>
          <path d="M4.5 10h11M5.3 7.2h9.4M5.3 12.8h9.4" stroke="#fff" stroke-width="0.9"/>
        </svg>
        <span>www.bramwellfa.com</span>
      </li>
    </ul>

    <svg class="accent-band" viewBox="0 0 580 12" preserveAspectRatio="none" aria-hidden="true">
      <polygon points="0,0 192,0 187,12 0,12" fill="var(--sky)"/>
      <polygon points="196,0 398,0 393,12 191,12" fill="var(--ocean)"/>
      <polygon points="402,0 580,0 580,12 397,12" fill="var(--deep)"/>
    </svg>
  </section>

  <section class="card card-back" aria-label="Business card back">
    <p class="brand-back">
      <span class="line line-lead">Bramwell</span>
      <span class="line line-sub">Financial Advisory Services Inc.</span>
    </p>
  </section>
</body>
</html>
```